Stylish Business Cards Wanted

- DOUBLE SIDED Design Required -

High end, edgy cards for a corporate and personal stylist. Must include logo,
Name: Belinda Harwick
Title: Director and Stylist
telephone : +61 8 7142 5809
email: belinda@theloombriefing.example
website: theloombriefing.example
Tag: Corporate Workwear & Uniform Specialist | Personal Stylist
Would like nice icons for telephone, email, website

Target Market(s)

Businesses wanting stylish uniforms, people wanting stylish wardrobes

Industry/Entity Type

Corporate Workwear Stylist

Contact Information for Business Card

I would like black, white and gold foiling incorporated in the design - possibly a touch of the other colours on my branding guide attached Name: Belinda Harwick Title: Director and Stylist telephone : +61 8 7142 5809 email: belinda@theloombriefing.example website: theloombriefing.example Tag: Corporate Workwear & Uniform Specialist | Personal Stylist Would like nice icons for telephone, email, website

Font styles to use
Other font styles liked:
• Raleway

Colors

Designer to choose colors to be used in the design.

Requirements
Must have
• Gold foil accents

```html
<!DOCTYPE html>
<html lang="en">
<head>
<meta charset="utf-8">
<title>The Loom Briefing — Business Cards</title>
<link rel="stylesheet" href="https://fonts.googleapis.com/css2?family=Raleway:wght@400;700&family=Arimo:wght@400&family=Great+Vibes&display=swap">
<style>
  :root {
    --backdrop: #e8e8e6;
    --card-black: #151515;
    --card-black-soft: #1e1e1e;
    --emboss: #262626;
    --gold: #e2b64a;
    --white: #f4f4f4;
  }
  * { margin: 0; padding: 0; box-sizing: border-box; }
  html, body {
    width: 1200px; height: 801px; overflow: hidden;
    background: var(--backdrop);
  }
  .sheet {
    position: relative; width: 1200px; height: 801px;
    display: flex; align-items: center; justify-content: center; gap: 40px;
  }
  .card {
    position: relative; width: 540px; height: 309px;
    background: var(--card-black);
    overflow: hidden;
    box-shadow: 0 6px 18px rgba(0,0,0,0.18);
  }

  /* Back: contact side */
  .card-back__watermark {
    position: absolute; left: 26px; top: 92px;
    font-family: "Raleway", sans-serif; font-weight: 700;
    font-size: 40px; line-height: 1.1; letter-spacing: 1px;
    color: var(--emboss);
    width: 220px;
  }
  .card-back__details {
    position: absolute; right: 30px; top: 46px;
    text-align: right;
  }
  .card-back__name {
    font-family: "Great Vibes", cursive;
    font-size: 40px; color: var(--gold); line-height: 1;
  }
  .card-back__title {
    font-family: "Arimo", sans-serif; font-size: 15px;
    color: var(--white); margin-top: 6px; margin-bottom: 34px;
  }
  .contact-list { list-style: none; }
  .contact-list__item {
    display: flex; align-items: center; justify-content: flex-end; gap: 10px;
    font-family: "Arimo", sans-serif; font-size: 14px; color: var(--white);
    line-height: 24px;
  }
  .contact-list__icon { width: 14px; height: 14px; flex: none; }

  /* Front: brand side */
  .card-front__pattern {
    position: absolute; inset: 0;
    background: radial-gradient(ellipse at 50% 45%, #242424 0%, var(--card-black-soft) 55%, var(--card-black) 100%);
  }
  .card-front__brand {
    position: absolute; left: 0; right: 0; top: 104px;
    text-align: center;
    font-family: "Raleway", sans-serif; font-weight: 700;
    font-size: 46px; letter-spacing: 1px; color: var(--gold);
  }
  .card-front__tagline {
    position: absolute; left: 0; right: 0; bottom: 30px;
    text-align: center;
    font-family: "Raleway", sans-serif; font-weight: 700;
    font-size: 13.5px; letter-spacing: 0.5px; color: var(--gold);
  }
</style>
</head>
<body>
<main class="sheet">

  <section class="card card-back" aria-label="Business card, contact side">
    <div class="card-back__watermark" aria-hidden="true">The Loom Briefing</div>
    <div class="card-back__details">
      <p class="card-back__name">Belinda Harwick</p>
      <p class="card-back__title">Director and Stylist</p>
      <ul class="contact-list">
        <li class="contact-list__item">+61 8 7142 5809
          <svg class="contact-list__icon" viewBox="0 0 14 14" aria-hidden="true">
            <circle cx="7" cy="7" r="7" fill="var(--gold)"/>
            <path d="M4.3 3.6c.4-.3.8-.3 1 .1l.7 1.2c.2.3.1.6-.2.8l-.4.3c.3.8 1 1.5 1.8 1.9l.3-.4c.2-.3.5-.3.8-.2l1.2.7c.4.2.4.6.1 1l-.5.6c-.4.4-1 .5-1.6.2-1.7-.8-3-2.1-3.7-3.8-.2-.6-.1-1.2.3-1.6z" fill="var(--card-black)"/>
          </svg>
        </li>
        <li class="contact-list__item">belinda@theloombriefing.example
          <svg class="contact-list__icon" viewBox="0 0 14 14" aria-hidden="true">
            <rect x="0.5" y="2.5" width="13" height="9" rx="1" fill="var(--gold)"/>
            <path d="M1 3.2 7 7.8l6-4.6" fill="none" stroke="var(--card-black)" stroke-width="1.1"/>
          </svg>
        </li>
        <li class="contact-list__item">www.theloombriefing.example
          <svg class="contact-list__icon" viewBox="0 0 14 14" aria-hidden="true">
            <circle cx="7" cy="7" r="7" fill="var(--gold)"/>
            <g fill="none" stroke="var(--card-black)" stroke-width="0.9">
              <circle cx="7" cy="7" r="4.4"/>
              <ellipse cx="7" cy="7" rx="1.9" ry="4.4"/>
              <path d="M2.6 7h8.8"/>
            </g>
          </svg>
        </li>
      </ul>
    </div>
  </section>

  <section class="card card-front" aria-label="Business card, brand side">
    <div class="card-front__pattern" role="img" aria-label="Embossed black-on-black flourish pattern covering the card"></div>
    <h1 class="card-front__brand">The Loom Briefing</h1>
    <p class="card-front__tagline">CORPORATE WORKWEAR | UNIFORM SPECIALIST | PERSONAL STYLIST</p>
  </section>

</main>
</body>
</html>
```